Brand Identity Stationary Package

Hello I'm looking for a full branding package for my Property Management Company. I have a logo but looking to have the following
Business Card
Email signature
Facebook cover photo
Letterhead (word.doc)
#10 Envelope
Pocket Folder - link to 9x12 pocket folder design specs https://www.printorbit-example.ca/marketing-materials/presentation-folders
would like everything to match and be brand identifiable. The company looks after residential properties/apartments and some commercial properties. Attached is a zip of the files.
For Business Card
Name: Gareth Lindqvist
Position: Operations Manager
Number: 1 (555) 384-2917
Email: Gareth@harborkey-example.ca
Website: Harborkey-example.ca
Property Management

```html
<!DOCTYPE html>
<html lang="en">
<head>
<meta charset="utf-8">
<title>Harborkey Envelope</title>
<link rel="stylesheet" href="https://fonts.googleapis.com/css2?family=Montserrat:wght@600&family=Source+Sans+3:wght@400&display=swap">
<style>
  :root {
    --backdrop: #d1d1d1;
    --brand-green: #80a642;
    --ink: #111111;
    --paper-light: #ffffff;
    --paper-edge: #ecebeb;
    --paper-text: #f4f4f4;
  }
  * { margin: 0; padding: 0; box-sizing: border-box; }
  html, body { width: 1200px; height: 1050px; overflow: hidden; }
  body {
    position: relative;
    background: var(--backdrop);
    font-family: "Source Sans 3", sans-serif;
  }
  .envelope {
    position: absolute;
    left: 145px;
    width: 910px;
    height: 390px;
    background: radial-gradient(ellipse at 50% 55%, var(--paper-light) 0%, var(--paper-light) 18%, var(--paper-edge) 75%);
    box-shadow: 0 14px 24px rgba(0,0,0,0.28);
    overflow: hidden;
  }
  .envelope--back { top: 105px; }
  .envelope--front { top: 556px; }
  .envelope-art { position: absolute; inset: 0; width: 910px; height: 390px; }
  .flap-name {
    position: absolute;
    top: 34px;
    left: 0;
    width: 910px;
    text-align: center;
    font-family: "Montserrat", sans-serif;
    font-weight: 600;
    font-size: 44px;
    letter-spacing: 5px;
    color: var(--paper-text);
  }
  .brand-name {
    position: absolute;
    left: 52px;
    top: 128px;
    font-family: "Montserrat", sans-serif;
    font-weight: 600;
    font-size: 40px;
    letter-spacing: 4px;
    color: var(--ink);
  }
  .contact-list {
    position: absolute;
    left: 52px;
    top: 220px;
    list-style: none;
  }
  .contact-item {
    display: flex;
    align-items: center;
    height: 26px;
    font-size: 20px;
    color: var(--ink);
  }
  .contact-icon {
    width: 16px;
    height: 16px;
    margin-right: 13px;
    fill: var(--brand-green);
  }
</style>
</head>
<body>

  <section class="envelope envelope--back" aria-label="Envelope back with flap">
    <svg class="envelope-art" viewBox="0 0 910 390" aria-hidden="true">
      <path d="M0 0 H910 L885 88 C870 118 845 131 827 131 H83 C65 131 40 118 25 88 Z" fill="var(--brand-green)"/>
    </svg>
    <div class="flap-name">HARBORKEY</div>
  </section>

  <section class="envelope envelope--front" aria-label="Envelope front with contact details">
    <svg class="envelope-art" viewBox="0 0 910 390" aria-hidden="true">
      <path d="M0 0 H910 V80 C840 60 760 57 640 60 C480 64 330 88 200 88 C110 88 45 75 0 61 Z" fill="var(--brand-green)"/>
      <path d="M0 69 C60 86 150 99 250 99 C320 99 380 92 412 84 C360 88 310 91 250 92 C150 92 60 78 0 83 Z" fill="var(--ink)"/>
      <path d="M0 68 V83 C60 98 150 101 250 99 C320 97 380 91 412 84 C340 90 300 92 250 92 C150 92 60 85 0 68 Z" fill="var(--ink)"/>
      <path d="M516 75 C600 69 720 64 780 65 C840 67 880 76 910 86 V100 C880 90 840 78 780 75 C700 72 600 73 516 75 Z" fill="var(--ink)"/>
      <path d="M0 306 C60 324 160 335 250 335 C310 335 360 333 394 331 C330 332 300 333 250 332 C150 330 60 318 0 316 Z" fill="var(--ink)"/>
      <path d="M0 306 V318 C60 330 160 336 250 335 C310 334 360 332 394 331 C330 331 290 330 250 329 C150 326 60 318 0 306 Z" fill="var(--ink)"/>
      <path d="M493 321 C600 311 720 305 780 305 C840 306 880 313 910 321 V339 C880 329 840 318 780 316 C700 314 600 318 493 321 Z" fill="var(--ink)"/>
      <path d="M0 326 C60 343 150 349 250 349 C380 348 520 333 640 329 C780 325 860 335 910 347 V390 H0 Z" fill="var(--brand-green)"/>
    </svg>

    <div class="brand-name">HARBORKEY</div>

    <ul class="contact-list">
      <li class="contact-item">
        <svg class="contact-icon" viewBox="0 0 16 16" aria-hidden="true"><path d="M1 6 C1 3 4 2 8 2 C12 2 15 3 15 6 L12 7 L11 5 H5 L4 7 Z M4 8 H12 L13 14 H3 Z"/></svg>
        1 (555) 384-2917
      </li>
      <li class="contact-item">
        <svg class="contact-icon" viewBox="0 0 16 16" aria-hidden="true"><path d="M1 3 H15 V13 H1 Z M2 4 L8 9 L14 4 Z" fill-rule="evenodd"/></svg>
        Gareth@harborkey-example.ca
      </li>
      <li class="contact-item">
        <svg class="contact-icon" viewBox="0 0 16 16" aria-hidden="true"><circle cx="8" cy="8" r="7"/><path d="M4 5 C6 4 7 6 6 8 C5 10 7 11 6 13 M10 3 C11 5 13 6 12 9" stroke="#fff" stroke-width="1.2" fill="none"/></svg>
        www.Harborkey-example.ca
      </li>
    </ul>
  </section>

</body>
</html>
```